QVR business card

Need a business card for a company that provides instructional design and elearning development services. The website is here: http://quorvane.studio/

I'm attaching a current logo, as well as the old business card design. While I like to keep it clean, the old design is too simplistic for my liking. The only idea I want to reuse from the old design is placing industry jargon on the back of the card, just need a better way to present it. But if you have other ideas for the back--feel free to experiment.

Please use the colors complementary to the color we have on the website. Thank you!

```html
<!DOCTYPE html>
<html lang="en">
<head>
<meta charset="utf-8">
<title>QVR Business Card</title>
<link rel="stylesheet" href="https://fonts.googleapis.com/css2?family=Arimo:wght@400;700&family=Montserrat:wght@600;700&display=swap">
<style>
  :root {
    --bg: #e6e7e9;
    --card: #ffffff;
    --ink: #3a3a3a;
    --teal: #1fa99a;
    --gold: #d9c98f;
    --charcoal: #3b3b3b;
    --rule: #3a3a3a;
  }
  * { box-sizing: border-box; margin: 0; padding: 0; }
  html, body { width: 1200px; height: 900px; overflow: hidden; background: var(--bg); }
  .canvas {
    width: 1200px; height: 900px;
    display: flex; flex-direction: column; align-items: center; justify-content: center; gap: 32px;
  }
  .card {
    position: relative;
    width: 660px; height: 377px;
    background: var(--card);
    border-radius: 22px;
    overflow: hidden;
    box-shadow: 0 6px 18px rgba(0,0,0,.12);
  }
  .card__band {
    position: absolute; left: 0; right: 0; bottom: 0; height: 16px;
    display: flex;
  }
  .card__band span:nth-child(1) { flex: 0 0 36%; background: var(--gold); }
  .card__band span:nth-child(2) { flex: 0 0 30%; background: var(--charcoal); }
  .card__band span:nth-child(3) { flex: 1; background: var(--teal); }

  /* Back: jargon */
  .jargon {
    position: absolute; left: 52px; top: 44px;
    list-style: none;
    font-family: "Arimo", Arial, sans-serif;
    color: var(--ink);
    font-size: 27px; line-height: 39px; letter-spacing: 2.4px;
    text-transform: uppercase;
  }
  .jargon__hook {
    font-family: "Montserrat", Arial, sans-serif;
    font-weight: 700; color: var(--teal);
    font-size: 31px; letter-spacing: 1.5px;
  }

  /* Front: contact */
  .contact {
    position: absolute; right: 44px; top: 40px;
    text-align: right;
    font-family: "Arimo", Arial, sans-serif;
  }
  .contact__name {
    font-family: "Montserrat", Arial, sans-serif;
    font-weight: 700; color: var(--teal);
    font-size: 21px; letter-spacing: 1px; text-transform: uppercase;
  }
  .contact__list { list-style: none; margin-top: 8px; }
  .contact__list li {
    display: flex; justify-content: flex-end; align-items: center; gap: 10px;
    font-size: 14px; line-height: 22px; color: var(--ink); letter-spacing: .5px;
  }
  .contact__list svg { width: 13px; height: 13px; }
  .contact__rule {
    position: absolute; left: 30px; top: 66px; width: 300px; height: 2px;
    background: var(--rule);
  }
  .brand {
    position: absolute; left: 52px; bottom: 62px;
    display: flex; align-items: center; gap: 18px;
  }
  .brand__mark { width: 40px; height: 40px; background: var(--teal); }
  .brand__name {
    font-family: "Montserrat", Arial, sans-serif;
    font-weight: 700; color: var(--teal);
    font-size: 78px; letter-spacing: 6px; line-height: 1;
  }
</style>
</head>
<body>
<main class="canvas">

  <section class="card card--back" aria-label="Card back">
    <ul class="jargon">
      <li>Mobile learning SCORM</li>
      <li>Instructional design LMS</li>
      <li>MOOCs eLearning HTML5</li>
      <li class="jargon__hook">How can we help?</li>
      <li>Adult learning theory</li>
      <li>Gamification classroom</li>
      <li>xAPI blended learning</li>
    </ul>
    <div class="card__band"><span></span><span></span><span></span></div>
  </section>

  <section class="card card--front" aria-label="Card front">
    <div class="contact__rule"></div>
    <div class="contact">
      <p class="contact__name">Marek Olvanis</p>
      <ul class="contact__list">
        <li>555-014-2273
          <svg viewBox="0 0 16 16" aria-hidden="true"><path fill="var(--teal)" d="M3.6 1.2l2.3 2.6-1.2 1.8c.9 2 2.6 3.7 4.6 4.6l1.8-1.2 2.6 2.3-1.4 2.3C6.9 13.4 2.6 9.1 1.2 3z"/></svg>
        </li>
        <li>www.quorvane.studio
          <svg viewBox="0 0 16 16" aria-hidden="true"><g fill="none" stroke="var(--teal)" stroke-width="1.4"><circle cx="8" cy="8" r="6.5"/><ellipse cx="8" cy="8" rx="2.8" ry="6.5"/><path d="M1.5 8h13"/></g></svg>
        </li>
        <li>molvanis@quorvane.studio
          <svg viewBox="0 0 16 16" aria-hidden="true"><g fill="none" stroke="var(--teal)" stroke-width="1.4"><rect x="1.5" y="3.5" width="13" height="9"/><path d="M1.5 3.5L8 9l6.5-5.5"/></g></svg>
        </li>
      </ul>
    </div>
    <div class="brand">
      <span class="brand__mark" aria-hidden="true"></span>
      <span class="brand__name">QVR</span>
    </div>
    <div class="card__band"><span></span><span></span><span></span></div>
  </section>

</main>
</body>
</html>
```